Marta's Dwellings website

We need a simple website for our property investment business in the UK. We basically need our contact details and brief description.We have the company logo already done (via ArtFlockly) so please use these:https://drive.google.com/drive/folders/1szJ3iRhelElZ40NIFT7w-c14MaY3Y_oV?usp=sharingYou could use some stock photos of UK houses for now.Let me know when to provide more detailed descriptions, etc

Coding

Coded - Design and coding required

Number of Pages Required

1 page

Colors

Designer to choose colors to be used in the design.

```html
<!DOCTYPE html>
<html lang="en">
<head>
<meta charset="utf-8">
<title>Marta's Dwellings</title>
<link href="https://fonts.googleapis.com/css2?family=Open+Sans:wght@400;600&family=Raleway:wght@300;400&display=swap" rel="stylesheet">
<style>
:root{
  --ink:#1c1c1c;
  --text:#555;
  --white:#fff;
  --band:#f3f3f3;
  --dark:#333333;
  --field:#d8d8d8;
  --star:#f5a623;
}
*{margin:0;padding:0;box-sizing:border-box}
html,body{width:1200px;height:3751px;overflow:hidden}
body{position:relative;font-family:"Open Sans",sans-serif;color:var(--ink);background:var(--white)}
.abs{position:absolute}
.brand{font-family:"Open Sans",sans-serif;font-weight:400;letter-spacing:.42em;text-transform:uppercase;white-space:nowrap}
.heading{font-family:"Raleway",sans-serif;font-weight:300;text-transform:uppercase;letter-spacing:.02em}
.photo{position:absolute}

/* header */
.site-header .brand{left:89px;top:116px;font-size:20px;color:var(--ink)}
.top-bar{top:36px;right:89px;display:flex;align-items:center;gap:28px;white-space:nowrap}
.top-contact{font-size:16px;color:#555;display:flex;align-items:center;gap:10px}
.nav{top:92px;right:89px;display:flex;gap:46px;font-size:16px;color:#333}
.nav a{color:inherit;text-decoration:none;padding-bottom:6px}
.nav a.active{border-bottom:3px solid var(--ink);font-weight:600}

/* hero */
.hero{left:0;top:166px;width:1200px;height:582px;background:linear-gradient(180deg,#3a3e3a 0%,#5b5442 45%,#3c3425 100%)}
.hero-title{left:84px;top:345px;font-family:"Raleway",sans-serif;font-weight:400;font-size:68px;color:var(--white);white-space:nowrap}
.hero-text{left:89px;top:436px;width:500px;font-size:19px;line-height:29px;color:#eee}
.btn-outline{left:89px;top:552px;width:186px;height:54px;border:2px solid var(--white);color:var(--white);font-size:24px;font-weight:600;display:flex;align-items:center;justify-content:center}
.hero-badge{left:393px;top:645px}
.hero-badge-name{left:393px;top:730px;width:422px;text-align:center;font-size:10px;letter-spacing:.45em;color:var(--ink)}

/* about */
.section-title{font-size:42px}
.body-copy{font-size:16px;line-height:27px;color:var(--text)}
.btn-dark{background:var(--ink);color:var(--white);font-size:21px;font-weight:600;display:flex;align-items:center;justify-content:center}

/* properties */
.properties{left:0;top:1369px;width:1200px;height:723px;background:var(--band)}
.card-caption{color:var(--white)}
.arrow{width:26px;height:26px;border-radius:50%;background:#111;display:flex;align-items:center;justify-content:center}

/* testimonials */
.testimonials{left:0;top:2092px;width:1200px;height:551px;background:linear-gradient(180deg,#2a2e24 0%,#3b3b2e 50%,#2c2620 100%)}
.quote-card{left:250px;top:2349px;width:675px;height:224px;background:var(--white);border-radius:6px;text-align:center}
.avatar{left:537px;top:2313px;width:108px;height:108px;border-radius:50%;background:linear-gradient(#c9c3bb,#8d8780);border:3px solid #444}

/* contact */
.field{position:absolute;border:1px solid var(--field);background:var(--white);font-size:13px;color:#444;padding:12px 12px}

/* footer */
.footer{left:0;top:3288px;width:1200px;height:463px;background:var(--dark)}
.footer-col-title{font-family:"Raleway",sans-serif;font-weight:400;font-size:27px;color:var(--white)}
.footer-link{font-size:16px;color:var(--white)}
</style>
</head>
<body>

<header class="site-header">
  <div class="abs brand">Marta's Dwellings</div>
  <div class="abs top-bar">
    <div class="top-contact">
      <svg width="24" height="18" viewBox="0 0 24 18"><rect x="1" y="1" width="22" height="16" fill="none" stroke="#222" stroke-width="2"/><path d="M1 1l11 9 11-9M1 17l8-7M23 17l-8-7" fill="none" stroke="#222" stroke-width="1.6"/></svg>
      <span>info@martasdwellings.example</span>
    </div>
    <div class="top-contact">
      <svg width="16" height="16" viewBox="0 0 16 16"><path d="M3 1l3 3-2 2c1 2 3 4 6 6l2-2 3 3-2 3C7 15 1 9 1 3z" fill="#222"/></svg>
      <span>888 888 888</span>
    </div>
  </div>
  <nav class="abs nav">
    <a class="active">Home</a><a>About Us</a><a>Our Properties</a><a>Blog</a><a>Contact Us</a>
  </nav>
</header>

<section>
  <div class="photo hero" role="img" aria-label="Dusk view of old stone English manor houses behind trees"></div>
  <h1 class="abs hero-title">Marta's Dwellings</h1>
  <p class="abs hero-text">Lorem ipsum dolor sit amet, consectetur adipiscing elit. Ut quis viverra tortor. Nunc luctus ornare arcu, at pulvinar mauris.</p>
  <div class="abs btn-outline">View More</div>
  <svg class="abs hero-badge" width="422" height="104" viewBox="0 0 422 104"><polygon points="0,104 207,0 422,104" fill="#fff" stroke="#111" stroke-width="6"/></svg>
  <div class="abs brand hero-badge-name">Marta's Dwellings</div>
</section>

<section>
  <h2 class="abs heading section-title" style="left:89px;top:912px">About Us</h2>
  <p class="abs body-copy" style="left:89px;top:1001px;width:510px">Lorem ipsum dolor sit amet, consectetur adipiscing elit. Ut quis viverra tortor. Nunc luctus ornare arcu, at pulvinar mauris. Sed libero eros, nsequat sed aliquam quis, placerat eu risus. Curabitur cursus id orci ut pretium. Donec scelerisque mi a semper dictum. Pellentesque abitant morbi tristique senectus et netus et malesuada fames ac turpis egestas.Aenean ut imperdiet leo.</p>
  <div class="abs btn-dark" style="left:89px;top:1217px;width:214px;height:57px">READ MORE</div>
  <svg class="abs" style="left:630px;top:822px" width="482" height="482" viewBox="0 0 482 482" role="img" aria-label="Red brick terraced houses with a green front garden">
    <polygon points="241,4 478,241 241,478 4,241" fill="#fff" stroke="#111" stroke-width="8"/>
    <polygon points="241,24 458,241 241,458 24,241" fill="#6f8a4a"/>
  </svg>
</section>

<section>
  <div class="abs properties"></div>
  <h2 class="abs heading section-title" style="left:0;top:1424px;width:1200px;text-align:center">Our Properties</h2>
  <div class="photo" role="img" aria-label="Row of Victorian brick houses under a blue sky" style="left:89px;top:1526px;width:505px;height:247px;background:linear-gradient(160deg,#3b4c7a,#8a5a48 55%,#4a3a30)"></div>
  <div class="abs card-caption" style="left:102px;top:1649px;font-family:Raleway,sans-serif;font-size:29px">Luxury family home</div>
  <div class="abs card-caption" style="left:102px;top:1693px;width:290px;font-size:16px;line-height:20px">12 Orchard Row, Hollinford, HF4 7QD, UK</div>
  <div class="abs card-caption" style="left:102px;top:1743px;font-size:14px;word-spacing:2px">Beds: 4 &nbsp;&nbsp;&nbsp; Bathroom: 3 &nbsp;&nbsp;&nbsp; Build: 54 - 145 m2</div>
  <svg class="abs" style="left:468px;top:1742px" width="110" height="20" viewBox="0 0 110 20"><circle cx="10" cy="10" r="9" fill="#222"/><circle cx="56" cy="10" r="9" fill="#222"/><circle cx="100" cy="10" r="9" fill="#222"/><path d="M10 14l-4-4a2 2 0 0 1 4-2 2 2 0 0 1 4 2z" fill="none" stroke="#fff"/><rect x="51" y="6" width="10" height="8" fill="none" stroke="#fff"/><path d="M96 10h8M100 6v8" stroke="#fff"/></svg>
  <div class="photo" role="img" aria-label="Georgian brick townhouse facade with red and pink front doors" style="left:603px;top:1526px;width:506px;height:247px;background:linear-gradient(160deg,#7a4b3c,#a96a55 50%,#5a3a30)"></div>
  <div class="photo" role="img" aria-label="Detached brick house with white garage doors" style="left:88px;top:1782px;width:251px;height:251px;background:linear-gradient(180deg,#7aa7d8,#9c7260 50%,#8a8a80)"></div>
  <div class="photo" role="img" aria-label="White new-build house under a cloudy sky" style="left:344px;top:1782px;width:251px;height:251px;background:linear-gradient(180deg,#8fb6e3,#d9dde2 50%,#7c8a70)"></div>
  <div class="photo" role="img" aria-label="Red brick semi-detached house with a small tree" style="left:602px;top:1782px;width:251px;height:251px;background:linear-gradient(180deg,#9a8c80,#8e4a36 45%,#6a5a48)"></div>
  <div class="photo" role="img" aria-label="Cream rendered house with bay windows" style="left:858px;top:1782px;width:251px;height:251px;background:linear-gradient(180deg,#a8c4e6,#e0d4b8 45%,#8a3a2c)"></div>
  <div class="abs arrow" style="left:28px;top:1751px"><svg width="14" height="12" viewBox="0 0 14 12"><path d="M13 6H3M7 1L2 6l5 5" stroke="#fff" stroke-width="2.4" fill="none"/></svg></div>
  <div class="abs arrow" style="left:1143px;top:1751px"><svg width="14" height="12" viewBox="0 0 14 12"><path d="M1 6h10M7 1l5 5-5 5" stroke="#fff" stroke-width="2.4" fill="none"/></svg></div>
</section>

<section>
  <div class="photo testimonials" role="img" aria-label="Darkened street of brick houses covered in ivy"></div>
  <h2 class="abs heading" style="left:0;top:2153px;width:1200px;text-align:center;font-size:40px;color:var(--white);font-weight:400">What Customers Say</h2>
  <p class="abs" style="left:180px;top:2231px;width:840px;text-align:center;font-size:17px;line-height:27px;color:var(--white)">Lorem ipsum dolor sit amet, consectetur adipiscing elit. Ut quis viverra tortor. Nunc luctus ornare arcu, at pulvinar mauris.</p>
  <div class="abs quote-card">
    <div style="margin-top:85px;font-family:Raleway,sans-serif;font-size:20px;color:#333">-Ms Pellow</div>
    <div style="color:var(--star);font-size:14px;letter-spacing:5px">★★★★★</div>
    <p style="margin:10px auto 0;width:480px;font-size:13.5px;line-height:22px;color:#444">Lorem ipsum dolor sit amet, consectetur adipiscing elit. Ut quis viverra tortor. Nunc luctus ornare arcu, at pulvinar mauris. Sed libero eros, consequat sed aliquam quis, placerat eu risus.</p>
  </div>
  <div class="abs avatar" role="img" aria-label="Portrait of the reviewer"></div>
  <svg class="abs" style="left:160px;top:2459px" width="24" height="24" viewBox="0 0 24 24"><circle cx="12" cy="12" r="10" fill="none" stroke="#fff" stroke-width="2"/><path d="M17 12H8M11 8l-4 4 4 4" fill="none" stroke="#fff" stroke-width="2"/></svg>
  <svg class="abs" style="left:990px;top:2459px" width="24" height="24" viewBox="0 0 24 24"><circle cx="12" cy="12" r="10" fill="none" stroke="#fff" stroke-width="2"/><path d="M7 12h9M13 8l4 4-4 4" fill="none" stroke="#fff" stroke-width="2"/></svg>
</section>

<section>
  <h2 class="abs heading section-title" style="left:0;top:2719px;width:1200px;text-align:center">Contact Us</h2>
  <p class="abs body-copy" style="left:140px;top:2800px;width:920px;text-align:center;font-size:17px">Lorem ipsum dolor sit amet, consectetur adipiscing elit. Ut quis viverra tortor. Nunc luctus ornare arcu, at pulvinar mauris. Sed libero eros, consequat sed aliquam quis, placerat eu risus.</p>
  <div class="field" style="left:121px;top:2897px;width:460px;height:40px">Name</div>
  <div class="field" style="left:604px;top:2897px;width:460px;height:40px">Email</div>
  <div class="field" style="left:121px;top:2951px;width:460px;height:40px">Phone Number</div>
  <div class="field" style="left:604px;top:2951px;width:460px;height:40px">Appointments</div>
  <div class="field" style="left:121px;top:3005px;width:943px;height:114px">Messages</div>
  <div class="abs btn-dark" style="left:494px;top:3173px;width:212px;height:56px">SUBMIT</div>
</section>

<footer>
  <div class="abs footer"></div>
  <div class="abs brand" style="left:89px;top:3432px;font-size:19px;color:var(--white)">Marta's Dwellings</div>
  <p class="abs" style="left:89px;top:3475px;width:320px;font-size:16px;line-height:27px;color:var(--white)">Lorem ipsum dolor sit amet, onsectetur adipiscing elit. Ut quis viverra tortor. Nunc luctus ornare arcu, at pulvinar mauris. Sed libero eros, consequat sed aliquam quis, placerat eu risus.</p>
  <div class="abs footer-col-title" style="left:505px;top:3425px">Quick Links</div>
  <div class="abs" style="left:506px;top:3481px;display:flex;flex-direction:column;gap:13px">
    <span class="footer-link">Home</span><span class="footer-link">About Us</span><span class="footer-link">Our Properties</span><span class="footer-link">Blog</span><span class="footer-link">Contact Us</span>
  </div>
  <div class="abs footer-col-title" style="left:759px;top:3425px">Contact Us</div>
  <svg class="abs" style="left:761px;top:3483px" width="12" height="16" viewBox="0 0 12 16"><path d="M6 0a6 6 0 0 1 6 6c0 4-6 10-6 10S0 10 0 6a6 6 0 0 1 6-6z" fill="#fff"/><circle cx="6" cy="6" r="2.2" fill="#333"/></svg>
  <p class="abs footer-link" style="left:791px;top:3479px;width:330px;line-height:32px">Unit 8, Linden Court, 14-16 Brookside Way, Ashcombe, Westshire, United Kingdom, AB12 3CD</p>
  <svg class="abs" style="left:760px;top:3581px" width="15" height="15" viewBox="0 0 16 16"><path d="M3 1l3 3-2 2c1 2 3 4 6 6l2-2 3 3-2 3C7 15 1 9 1 3z" fill="#fff"/></svg>
  <div class="abs footer-link" style="left:791px;top:3580px">888 888 888</div>
  <svg class="abs" style="left:760px;top:3618px" width="16" height="12" viewBox="0 0 16 12"><rect width="16" height="12" fill="#fff"/><path d="M0 0l8 6 8-6" fill="none" stroke="#333" stroke-width="1.5"/></svg>
  <div class="abs footer-link" style="left:791px;top:3613px">info@martasdwellings.example</div>
  <div class="abs" style="left:0;top:3697px;width:1200px;text-align:center;font-size:16px;color:var(--white)">Copyright © 2019 Marta's Dwellings.All rights reserved</div>
</footer>

</body>
</html>
```